Boutique Real Estate Brokerage Tessly Realty Website Design

Winning designer work on migrate as well through nest ferry.
We need a new website as an informational hub to aid our print and digital strategy as well as showing that we are located in Brooklyn and Florida. I have a boutique real estate brokerage and advisory firm specializing in residential leasing, multifamily sales and 1031 Exchange appropriation. This won't be a portal to search properties, it will be a place for information. I'd like space for an ebook to be downloaded and information on my probate sales and multifamily leasing marketing campaigns. I included my logo and will leave it up to the designer to come up with colors to match it. I have also attached verbiage for each page. The final design should have a modern high end look that reflects gentrifying Brooklyn as well as beautiful Florida.
Thank you!
Target Market(s)
Owners of income producing real estate and develop-able land in Brooklyn, NY and Florida.
Industry/Entity Type
Real Estate
Coding
Coded - Design and coding required
Number of Pages Required
5+ page
Colors
Designer to choose colors to be used in the design.
Requirements
Must have
- A modern elegant look
Nice to have
- pictures of brooklyn and florida
Should not have
- real estate search pages

```html
<!DOCTYPE html>
<html lang="en">
<head>
<meta charset="utf-8">
<title>Tessly Realty</title>
<link href="https://fonts.googleapis.com/css2?family=Saira:wght@500;600;700&family=Open+Sans:wght@400;600&display=swap" rel="stylesheet">
<style>
:root{
  --black:#000;
  --ink:#1b1b1b;
  --white:#fff;
  --grey-dark:#3a3a3c;
  --grey-mid:#6b6b6e;
  --grey-light:#a7a7a7;
  --line:#9a9a9a;
  --field:#4a4a4c;
  --brick:#7a5a48;
  --leaf:#4f6a3a;
  --sky:#8fb0cf;
  --water:#3f5460;
}
*{box-sizing:border-box;margin:0;padding:0}
html,body{width:1200px;height:3529px;overflow:hidden}
body{position:relative;background:var(--white);font-family:"Open Sans",sans-serif;color:var(--ink)}
.heading{font-family:"Saira",sans-serif;font-weight:600;text-transform:uppercase}
.abs{position:absolute}

/* header */
.site-header{left:0;top:0;width:1200px;height:110px;background:var(--black)}
.brand{left:165px;top:34px;display:flex;align-items:center;gap:14px;color:var(--white);font-family:"Saira",sans-serif;font-weight:600;font-size:20px;letter-spacing:3px}
.brand-mark{width:38px;height:38px;border-radius:50%;background:var(--grey-light)}
.main-nav{left:552px;top:42px;display:flex;gap:34px;font-family:"Saira",sans-serif;font-weight:600;font-size:16px;color:var(--white)}
.main-nav a{color:var(--white);text-decoration:none}

/* hero */
.hero{left:0;top:110px;width:1200px;height:562px}
.hero-title{left:0;top:175px;width:1200px;text-align:center;color:var(--white);font-size:42px;line-height:49px}
.hero-dots{left:558px;top:508px;display:flex;gap:12px}
.hero-dots span{width:18px;height:18px;border:2px solid var(--white);border-radius:50%}
.hero-dots span.active{background:var(--white)}

/* services */
.section-title{width:1200px;left:0;text-align:center;font-size:29px;color:var(--ink)}
.service-card{top:790px;width:361px;height:263px}
.service-photo{width:100%;height:100%}
.service-label{position:absolute;left:8px;right:8px;bottom:8px;height:56px;background:var(--black);color:var(--white);display:flex;align-items:center;justify-content:center;font-size:19px}

/* story */
.story-photo{left:480px;top:1150px;width:720px;height:522px;background:linear-gradient(160deg,#c9d3da 0%,#8c6f5f 45%,#5c4a40 75%,#2f2f30 100%)}
.story-panel{left:0;top:1165px;width:670px;height:507px;background:linear-gradient(90deg,var(--grey-dark),var(--grey-mid));clip-path:polygon(0 0,100% 0,67% 100%,0 100%)}
.story-title{left:100px;top:1245px;color:var(--white);font-size:30px}
.story-text{left:100px;top:1300px;width:450px;color:#e6e6e6;font-size:14px;line-height:24px}
.btn-outline{display:flex;align-items:center;justify-content:center;border:2px solid var(--white);color:var(--white);font-family:"Saira",sans-serif;font-weight:600;font-size:16px;text-transform:uppercase}
.story-btn{left:100px;top:1505px;width:168px;height:46px}

/* mortgage tools */
.tool-card{top:1843px;width:336px;height:327px;border:2px solid var(--line);background:var(--white)}
.tool-card.dark{background:linear-gradient(180deg,#111 0%,#4a4a4c 100%);border-color:#555;color:var(--white)}
.tool-tab{position:absolute;left:50%;top:-46px;width:92px;height:92px;margin-left:-46px;border-radius:50%;border:2px solid var(--line);background:var(--white);clip-path:inset(0 0 47px 0);display:flex;justify-content:center;padding-top:14px}
.tool-card.dark .tool-tab{background:var(--black);border-color:#555}
.tool-title{position:absolute;left:0;top:38px;width:100%;text-align:center;font-size:19px}
.rates{position:absolute;left:34px;top:120px;font-size:14px;border-collapse:collapse}
.rates th{font-weight:600;font-size:13px;text-align:left;padding:0 0 10px 20px}
.rates td{padding:4px 0 4px 20px}
.rates td:first-child{padding-left:0}
.rates-link{position:absolute;left:34px;top:250px;font-size:13px;font-weight:600}
.calc-label{position:absolute;left:38px;font-size:13px;color:#ddd}
.calc-field{position:absolute;left:38px;height:38px;background:var(--field);color:#eee;font-size:15px;padding:9px 12px}
.calc-btn{position:absolute;left:176px;top:225px;width:130px;height:38px;font-size:14px}
.areas{position:absolute;left:0;top:112px;width:100%;text-align:center;font-size:15px;line-height:28px;list-style:none}

/* ebook band */
.ebook{left:0;top:2270px;width:1200px;height:385px;background:linear-gradient(180deg,#2b2b2b 0%,#5b5b5b 45%,#1c1c1c 100%);border-top:3px solid #2a3c70}
.ebook-title{left:0;top:2380px;width:1200px;text-align:center;color:var(--white);font-size:33px;line-height:38px}
.ebook-btn{left:500px;top:2478px;width:200px;height:49px;font-size:19px}

/* contact */
.contact-photo{left:420px;top:2655px;width:780px;height:498px;background:linear-gradient(90deg,#ffffff 0%,#e6e6e6 18%,#a9a9a9 45%,#7c7c7c 70%,#b9b9b9 100%)}
.contact-title{left:120px;top:2725px;font-size:27px}
.field{position:absolute;border:2px solid var(--grey-dark);background:var(--white);font-size:15px;color:#444;padding:0 20px;display:flex;align-items:center}
.field.area{align-items:flex-start;padding-top:10px}
.submit-btn{left:120px;top:3040px;width:150px;height:49px;border:2px solid var(--black);display:flex;align-items:center;justify-content:center;font-size:18px}

/* footer */
.site-footer{left:0;top:3153px;width:1200px;height:376px;background:var(--black);color:var(--white)}
.footer-brand{left:150px;top:3282px;display:flex;align-items:center;gap:10px;font-family:"Saira",sans-serif;font-weight:600;font-size:16px;letter-spacing:2px;color:var(--white)}
.footer-mark{width:24px;height:24px;border-radius:50%;background:var(--grey-light)}
.footer-col-title{font-size:17px}
.footer-list{list-style:none;font-size:14px;line-height:26px}
.contact-item{display:flex;gap:14px;font-size:14px;line-height:20px;margin-bottom:16px}
.contact-item svg{flex:none;margin-top:2px}
.social-item{display:flex;align-items:center;gap:12px;font-size:14px;margin-bottom:10px}
.social-dot{width:24px;height:24px;border-radius:50%;background:var(--white)}
.footer-rule{left:0;top:3462px;width:1200px;height:1px;background:#2a2a2a}
.copyright{left:0;top:3484px;width:1200px;text-align:center;font-size:13px;color:#888}
</style>
</head>
<body>

<header class="site-header abs">
  <div class="brand abs"><span class="brand-mark"></span>TESSLY REALTY</div>
  <nav class="main-nav abs">
    <a href="#">HOME</a><a href="#">ABOUT US</a><a href="#">SERVICES</a><a href="#">SIGN UP</a><a href="#">CONTACT</a>
  </nav>
</header>

<section class="hero abs">
  <svg width="1200" height="562" role="img" aria-label="Brooklyn brownstone stoop beside a Florida waterfront apartment complex">
    <defs>
      <linearGradient id="heroLeft" x1="0" y1="0" x2="1" y2="1">
        <stop offset="0" stop-color="#6b4a3a"/><stop offset="0.6" stop-color="#4a3328"/><stop offset="1" stop-color="#2a211c"/>
      </linearGradient>
      <linearGradient id="heroRight" x1="0" y1="0" x2="0" y2="1">
        <stop offset="0" stop-color="#9fc0de"/><stop offset="0.35" stop-color="#c9a27e"/><stop offset="0.55" stop-color="#4f6a3a"/><stop offset="1" stop-color="#34474f"/>
      </linearGradient>
    </defs>
    <rect width="1200" height="562" fill="url(#heroRight)"/>
    <polygon points="0,0 700,0 540,562 0,562" fill="url(#heroLeft)"/>
  </svg>
</section>
<h1 class="hero-title heading abs" style="top:285px">Assisting landlords<br>increase profits while<br>decreasing the stress</h1>
<div class="hero-dots abs"><span></span><span class="active"></span><span></span></div>

<h2 class="section-title heading abs" style="top:722px">How we can help</h2>
<div class="service-card abs" style="left:42px">
  <div class="service-photo" role="img" aria-label="Bright apartment interior with kitchen" style="background:linear-gradient(135deg,#e8e6e2,#9a9a96 60%,#5a5a58)"></div>
  <div class="service-label heading">Multi-family leasing</div>
</div>
<div class="service-card abs" style="left:423px">
  <div class="service-photo" role="img" aria-label="Brick multifamily building with fire escapes" style="background:linear-gradient(160deg,#c9d7e3,#b38a6c 45%,#6e4c3a)"></div>
  <div class="service-label heading">Multi-family sales</div>
</div>
<div class="service-card abs" style="left:804px">
  <div class="service-photo" role="img" aria-label="Aerial view of a Florida town and land parcels" style="background:linear-gradient(180deg,#a9c4df,#9aa68a 40%,#5e6e4e)"></div>
  <div class="service-label heading">Site selection advisory</div>
</div>

<div class="story-photo abs" role="img" aria-label="Brooklyn brownstone street with parked cars and bare trees"></div>
<div class="story-panel abs"></div>
<h2 class="story-title heading abs">Our story</h2>
<p class="story-text abs">Tessly Realty NYC specializes in assisting landlords by increasing their profits while decreasing their stress Aliquam Mauris nunc quam venenatis nec euismod sit amet egestas placerat est Pellentesque habitant morbi tristique senectus et netus et malesuada fames ac turpis egestas Cras id elit Integer quis urna Ut ante enim dapibus malesuada fringilla eu condimentum quis</p>
<a class="btn-outline story-btn abs">Read more</a>

<h2 class="section-title heading abs" style="top:1727px">Mortgage tools</h2>

<div class="tool-card abs" style="left:89px">
  <div class="tool-tab">
    <svg width="44" height="30" viewBox="0 0 44 30" fill="none" stroke="#222" stroke-width="2"><path d="M4 14 L18 3 L32 14"/><rect x="8" y="13" width="20" height="16"/><rect x="15" y="19" width="6" height="10"/><circle cx="36" cy="22" r="6"/></svg>
  </div>
  <h3 class="tool-title heading">Mortgage rates</h3>
  <table class="rates">
    <tr><th style="padding-left:0"></th><th>CURRENT</th><th>LAST WEEK</th></tr>
    <tr><td>30 YEAR FIXED</td><td>4.19%</td><td>4.17%</td></tr>
    <tr><td>15 YEAR FIXED</td><td>3.62%</td><td>3.64%</td></tr>
    <tr><td>5/1 ADJUSTABLE</td><td>3.92%</td><td>3.97%</td></tr>
  </table>
  <p class="rates-link">Current Mortgage Rates</p>
</div>

<div class="tool-card dark abs" style="left:440px">
  <div class="tool-tab">
    <svg width="30" height="32" viewBox="0 0 30 32" fill="none" stroke="#fff" stroke-width="2"><rect x="2" y="1" width="26" height="30" rx="2"/><rect x="6" y="5" width="18" height="7"/><path d="M7 17h4M13 17h4M19 17h4M7 22h4M13 22h4M19 22h4M7 27h4M13 27h4M19 27h4"/></svg>
  </div>
  <h3 class="tool-title heading">Mortgage calculator</h3>
  <span class="calc-label" style="top:124px">HOME PRICE</span>
  <div class="calc-field" style="top:148px;width:268px">$</div>
  <span class="calc-label" style="top:210px">DOWN PAYMENT</span>
  <div class="calc-field" style="top:225px;width:128px">$</div>
  <a class="btn-outline calc-btn">Continue</a>
</div>

<div class="tool-card abs" style="left:788px">
  <div class="tool-tab">
    <svg width="30" height="32" viewBox="0 0 30 32" fill="none" stroke="#222" stroke-width="2"><path d="M15 26 C8 18 6 14 6 10 A9 9 0 0 1 24 10 C24 14 22 18 15 26Z"/><circle cx="15" cy="10" r="3"/><ellipse cx="15" cy="28" rx="11" ry="3"/></svg>
  </div>
  <h3 class="tool-title heading">Coverage areas</h3>
  <ul class="areas"><li>11221</li><li>11233</li><li>11238</li><li>11216</li><li>11207</li><li>11208</li></ul>
</div>

<section class="ebook abs" role="img" aria-label="Black and white night skyline across the river with bridge"></section>
<h2 class="ebook-title heading abs">Ebook for probate sales and multifamily<br>leasing marketing campaigns</h2>
<a class="btn-outline ebook-btn abs">Download</a>

<div class="contact-photo abs" role="img" aria-label="Black and white aerial view of Florida high-rise towers by the beach"></div>
<h2 class="contact-title heading abs">Contact form</h2>
<div class="field" style="left:120px;top:2783px;width:495px;height:47px">Full Name</div>
<div class="field" style="left:120px;top:2840px;width:245px;height:48px">Email</div>
<div class="field" style="left:370px;top:2840px;width:245px;height:48px">Phone</div>
<div class="field area" style="left:120px;top:2897px;width:495px;height:128px">Message</div>
<a class="submit-btn heading abs">Submit</a>

<footer class="site-footer abs"></footer>
<div class="footer-brand abs"><span class="footer-mark"></span>TESSLY REALTY</div>

<div class="abs" style="left:458px;top:3208px;color:#fff;width:280px">
  <h4 class="footer-col-title heading" style="margin-bottom:24px">Contact us</h4>
  <div class="contact-item">
    <svg width="14" height="18" viewBox="0 0 14 18" fill="none" stroke="#fff" stroke-width="1.5"><path d="M7 17 C2 11 1 8 1 6 A6 6 0 0 1 13 6 C13 8 12 11 7 17Z"/><circle cx="7" cy="6" r="2"/></svg>
    <span>482 Marlow Ave, 2, Brooklyn,<br>New York 11221</span>
  </div>
  <div class="contact-item">
    <svg width="16" height="16" viewBox="0 0 16 16" fill="none" stroke="#fff" stroke-width="1.5"><path d="M3 1 L6 1 L7 5 L5 6.5 C6 9 7 10 9.5 11 L11 9 L15 10 L15 13 C15 14 14 15 13 15 C6 15 1 10 1 3 C1 2 2 1 3 1Z"/></svg>
    <span>561-555-0142</span>
  </div>
  <div class="contact-item">
    <svg width="16" height="12" viewBox="0 0 16 12" fill="none" stroke="#fff" stroke-width="1.5"><rect x="1" y="1" width="14" height="10"/><path d="M1 1 L8 7 L15 1"/></svg>
    <span>hello@tesslyrealty.com</span>
  </div>
</div>

<div class="abs" style="left:765px;top:3208px;color:#fff">
  <h4 class="footer-col-title heading" style="margin-bottom:14px">Company</h4>
  <ul class="footer-list"><li>Home</li><li>About us</li><li>Services</li><li>Sign Up</li><li>Contact</li></ul>
</div>

<div class="abs" style="left:948px;top:3208px;color:#fff">
  <h4 class="footer-col-title heading" style="margin-bottom:18px">Get in touch</h4>
  <div class="social-item"><span class="social-dot"></span>Chirpline</div>
  <div class="social-item"><span class="social-dot"></span>Friendbook</div>
  <div class="social-item"><span class="social-dot"></span>WorkLinks</div>
  <div class="social-item"><span class="social-dot"></span>Snapgram</div>
</div>

<div class="footer-rule abs"></div>
<p class="copyright abs">Copyright © 2019 All right reserved</p>

</body>
</html>
```